Kestrel Facilities Business Card Design

We would now like to design business cards with the new Kestrel Facilities logo

Target Market(s)

Professional

Industry/Entity Type

Professional services

Contact Information for Business Card

Employee name, title, phone number, email address, corporate office address and logo.

Font styles to use
Sans Serif

Colors
0054AA
0677BA
7BADD7
CADEEF
E8F1F8

Requirements
Must have
• My logo
Should not have
• any other pictures or images besides my logo

```html
<!DOCTYPE html>
<html lang="en">
<head>
<meta charset="utf-8">
<title>Kestrel Facilities Business Card</title>
<link rel="stylesheet" href="https://fonts.googleapis.com/css2?family=Open+Sans:wght@400;600;700&display=swap">
<style>
  :root {
    --backdrop: #3b3b3c;
    --card: #1b1b1d;
    --blue: #3a7fcf;
    --white: #f2f2f2;
    --emboss: #5e5f62;
  }
  * { margin: 0; padding: 0; box-sizing: border-box; }
  html, body { width: 1200px; height: 801px; overflow: hidden; }
  body {
    background: var(--backdrop);
    font-family: "Open Sans", Arial, sans-serif;
    position: relative;
  }
  .card {
    position: absolute;
    width: 520px;
    height: 297px;
    background: var(--card);
    border-bottom: 3px solid var(--blue);
    box-shadow: 0 18px 40px rgba(0,0,0,0.45);
  }
  .card-front { left: 60px; top: 120px; }
  .card-back { left: 620px; top: 384px; }

  .brand {
    position: absolute;
    display: flex;
    align-items: center;
    gap: 10px;
    font-weight: 700;
    text-transform: uppercase;
    letter-spacing: 0.04em;
  }
  .brand-mark { display: block; }
  .card-front .brand { right: 34px; top: 34px; color: var(--blue); font-size: 20px; }
  .card-front .brand-mark { width: 40px; height: 40px; background: var(--blue); }
  .card-back .brand {
    left: 50%; top: 50%; transform: translate(-50%, -50%);
    color: var(--emboss); font-size: 28px; white-space: nowrap;
  }
  .card-back .brand-mark { width: 54px; height: 54px; background: var(--emboss); }

  .divider {
    position: absolute;
    left: 34px; right: 34px; top: 110px;
    height: 1px; background: var(--blue);
  }
  .address {
    position: absolute;
    right: 34px; top: 124px;
    text-align: right;
    color: var(--white);
    font-size: 13px;
    line-height: 1.45;
  }
  .person { position: absolute; left: 34px; top: 180px; }
  .person-name {
    color: var(--blue);
    font-size: 19px;
    font-weight: 700;
    text-transform: uppercase;
    letter-spacing: 0.01em;
    line-height: 1.1;
  }
  .person-title { color: var(--white); font-size: 13px; margin-top: 2px; }
  .contact-rule {
    position: absolute;
    left: 34px; top: 228px;
    width: 240px; height: 1px; background: var(--blue);
  }
  .contacts {
    position: absolute;
    left: 34px; top: 236px;
    list-style: none;
    color: var(--white);
    font-size: 13px;
    line-height: 17px;
  }
  .contacts li { display: flex; align-items: center; gap: 8px; }
  .contacts svg { width: 11px; height: 11px; fill: var(--blue); }
</style>
</head>
<body>
  <section class="card card-front" aria-label="Business card front">
    <div class="brand"><span class="brand-mark"></span>Kestrel Facilities</div>
    <div class="divider"></div>
    <p class="address">48 Millbrook Lane<br>Fairhaven, ST 021</p>
    <div class="person">
      <h1 class="person-name">Dana Whitlow</h1>
      <p class="person-title">CEO</p>
    </div>
    <div class="contact-rule"></div>
    <ul class="contacts">
      <li><svg viewBox="0 0 12 12" aria-hidden="true"><path d="M2.5 1 4.5 1 5.3 3.6 4 4.6C4.6 6 6 7.4 7.4 8L8.4 6.7 11 7.5 11 9.5C11 10.4 10.4 11 9.5 11 5 11 1 7 1 2.5 1 1.6 1.6 1 2.5 1Z"/></svg>555-014-2290</li>
      <li><svg viewBox="0 0 12 12" aria-hidden="true"><path d="M1 3 6 6.5 11 3 11 10 1 10Z M1.5 2 10.5 2 6 5Z"/></svg>dwhitlow@kestrelfm.com</li>
      <li><svg viewBox="0 0 12 12" aria-hidden="true"><circle cx="6" cy="6" r="5"/></svg>www.kestrelfm.com</li>
    </ul>
  </section>

  <section class="card card-back" aria-label="Business card back">
    <div class="brand"><span class="brand-mark"></span>Kestrel Facilities</div>
  </section>
</body>
</html>
```